ember-ridge builders and works

I need a web design for my company we offer counter tops. tile for floors,showers,kitchen backsplashes and more also need a place where the client
can write reviews

Tile

```html
<!DOCTYPE html>
<html lang="en">
<head>
<meta charset="utf-8">
<title>Ember-Ridge Builders and Works</title>
<link href="https://fonts.googleapis.com/css2?family=Arimo:ital,wght@0,400;0,700;1,400&family=Tinos:ital@1&display=swap" rel="stylesheet">
<style>
:root{
  --red:#a80000;
  --orange:#e5572c;
  --ink:#333;
  --muted:#777;
  --line:#e2e2e2;
  --panel:#f6f6f6;
  --footer:#353535;
  --white:#fff;
}
*{box-sizing:border-box;margin:0;padding:0}
html,body{width:1200px;height:1046px;overflow:hidden;background:var(--white)}
body{font-family:"Arimo",Arial,sans-serif;color:var(--ink);position:relative}
.top-rule{height:5px;background:#333}
.tool-tab{position:absolute;left:0;top:46px;width:35px;height:33px;background:#ddd;display:flex;align-items:center;justify-content:center}
.page{position:absolute;left:183px;width:840px;top:0}
.header{position:absolute;top:28px;left:0;width:840px;height:36px}
.brand{position:absolute;left:0;top:2px;font-size:22px;color:#444;letter-spacing:-.3px;white-space:nowrap}
.slogan{position:absolute;left:383px;top:13px;font-size:11px;color:#999;white-space:nowrap}
.contact{position:absolute;right:92px;top:13px;font-size:11px;display:flex;gap:20px;align-items:center;white-space:nowrap}
.contact .mail{color:var(--orange)}
.contact span{display:flex;gap:6px;align-items:center}
.social{display:flex;gap:4px}
.social i{display:block;width:21px;height:21px;border-radius:50%;background:#9a9a9a}
.header .social{position:absolute;right:10px;top:6px;background:#eee;padding:2px 3px}
.nav{position:absolute;top:84px;left:0;width:840px;height:37px;border:1px solid var(--line);background:linear-gradient(#fff,#f3f3f3);display:flex}
.nav a{width:93px;border-right:1px solid var(--line);display:flex;align-items:center;justify-content:center;font-size:11px;font-weight:700;color:#333;text-decoration:none}
.nav a.active{background:var(--red);color:#fff;border:2px solid #d9a0a0}
.nav .social{position:absolute;right:8px;top:7px}
.hero{position:absolute;top:136px;left:0;width:840px;height:312px;background:linear-gradient(100deg,#3b3432 0%,#8a7f74 30%,#d6b98a 55%,#c99a5e 75%,#e6ece8 100%)}
.caption{position:absolute;left:0;top:178px;width:313px;height:97px;background:var(--red);color:#fff;padding:20px 18px}
.caption h2{font-size:17px;font-weight:700;margin-bottom:10px}
.caption p{font-size:10.5px;line-height:16px}
.dots{position:absolute;left:0;top:275px;width:87px;height:23px;background:#222;display:flex;gap:7px;align-items:center;padding-left:13px}
.dots i{width:6px;height:6px;background:#fff}
.dots i.on{background:var(--red)}
.arrows{position:absolute;right:0;top:276px;display:flex;gap:2px}
.arrows b{width:22px;height:22px;background:var(--orange);display:flex;align-items:center;justify-content:center}
.callout{position:absolute;top:461px;left:0;width:840px;height:86px;background:var(--panel);border:1px solid var(--line);border-left:3px solid var(--orange);padding:16px 20px}
.callout h3{font-size:16px;font-weight:700;margin-bottom:6px}
.callout p{font-size:10.5px;line-height:16px;width:655px;color:#444}
.btn{position:absolute;background:var(--red);color:#fff;text-decoration:none;display:flex;align-items:center;justify-content:center}
.callout .btn{right:18px;top:14px;width:118px;height:37px;font-size:15px}
.section-head{position:absolute;left:0;font-size:16px;font-weight:700;white-space:nowrap}
.section-head em{font-weight:400;font-size:10px;color:var(--orange)}
.rule{position:absolute;height:1px;background:var(--line)}
.pager{position:absolute;display:flex;gap:1px}
.pager b{width:17px;height:17px;background:#ccc;display:flex;align-items:center;justify-content:center}
.pager b+b{background:#aaa}
.projects{position:absolute;top:631px;left:0;width:840px;display:flex;gap:17px}
.project{width:197px;text-align:center}
.project .photo{height:117px;position:relative}
.project h4{font-size:12px;font-weight:700;margin-top:12px}
.side-arrow{position:absolute;top:48px;width:20px;height:20px;background:var(--orange)}
.newsletter p{position:absolute;top:868px;left:0;width:410px;font-size:10.5px;line-height:17px}
.email{position:absolute;top:918px;left:0;width:325px;height:26px;background:var(--panel);border:1px solid var(--line);font-size:10.5px;color:#999;padding:6px 10px}
.newsletter .btn{left:335px;top:918px;width:77px;height:26px;font-size:11px}
.note{position:absolute;top:956px;left:0;font-size:9px;font-style:italic;color:#888}
.note b{color:var(--orange);font-weight:400}
.quote{position:absolute;top:868px;left:429px;width:411px;height:84px;border:1px solid #ddd;background:var(--panel);padding:14px 16px 0 36px;font-family:"Tinos",Georgia,serif;font-style:italic;font-size:12.5px;line-height:19px;color:#666}
.quote::before{content:"\201C";position:absolute;left:13px;top:6px;font-size:30px;color:#bbb}
.author{position:absolute;top:963px;right:56px;text-align:right;font-size:10.5px;line-height:16px}
.author span{display:block;color:#888}
.footer{position:absolute;left:0;top:1011px;width:1200px;height:35px;background:var(--footer);color:#bbb;font-size:9.5px}
.footer .copy{position:absolute;left:180px;top:14px}
.footer .links{position:absolute;right:182px;top:14px;color:#ddd}
.to-top{position:absolute;right:19px;top:1px;width:25px;height:22px;background:#888;display:flex;align-items:center;justify-content:center}
</style>
</head>
<body>
<div class="top-rule"></div>
<div class="tool-tab" aria-hidden="true">
  <svg width="22" height="22" viewBox="0 0 22 22"><path d="M4 18 L14 8 M8 4 L18 14" stroke="#333" stroke-width="3" stroke-linecap="round"/></svg>
</div>

<div class="page">
  <header class="header">
    <div class="brand">Ember-Ridge Builders and Works</div>
    <div class="slogan" style="left:360px;top:-12px;display:none"></div>
    <div class="contact">
      <span class="mail"><svg width="12" height="9"><rect x=".5" y=".5" width="11" height="8" fill="none" stroke="#aaa"/><path d="M1 1 L6 5 L11 1" fill="none" stroke="#aaa"/></svg>hello@emberridge-works.test</span>
      <span><svg width="12" height="12" viewBox="0 0 12 12"><path d="M2 1 L4 1 L5 4 L3.5 5 Q5 8 7 8.5 L8 7 L11 8 L11 10 Q6 12 2 6 Q1 3 2 1Z" fill="#999"/></svg>(555) 214-3098</span>
    </div>
    <div class="social"><i></i><i></i><i></i></div>
  </header>

  <nav class="nav">
    <a class="active" href="#">Home</a><a href="#">Tiles</a><a href="#">Systems</a><a href="#">Gallery</a><a href="#">About</a><a href="#">Contact us</a>
    <div class="social"><i></i><i></i><i></i></div>
  </nav>

  <section class="hero" role="img" aria-label="Bright modern living and dining room with wooden floor and large windows">
    <div class="caption">
      <h2>Clean Design Tiles</h2>
      <p>You can describe your slides using captions. This is an example of a caption with a link.</p>
    </div>
    <div class="dots"><i></i><i class="on"></i><i></i><i></i><i></i></div>
    <div class="arrows">
      <b><svg width="8" height="10"><path d="M6 1 L2 5 L6 9" stroke="#fff" fill="none" stroke-width="1.5"/></svg></b>
      <b><svg width="8" height="10"><path d="M2 1 L6 5 L2 9" stroke="#fff" fill="none" stroke-width="1.5"/></svg></b>
    </div>
  </section>

  <section class="callout">
    <h3>We offer counter tops. tile for floors, showers, kitchen backsplashes and more..</h3>
    <p>Lorem ipsum dolor sit amet, consectetuer adipiscing elit, sed diam nonummy nibh euismod tincidunt ut laoreet dolore magna aliquam erat volutpat sed diam nonummy.</p>
    <a class="btn" href="#">Learn More</a>
  </section>

  <h2 class="section-head" style="top:575px">Selected Projects <em>– View All Projects »</em></h2>
  <div class="pager" style="right:0;top:577px"><b></b><b><svg width="6" height="8"><path d="M1 1 L5 4 L1 7" stroke="#fff" fill="none"/></svg></b></div>
  <div class="rule" style="top:608px;left:0;width:840px"></div>

  <section class="projects">
    <article class="project"><div class="photo" role="img" aria-label="White dining room with table and chairs" style="background:linear-gradient(135deg,#9fb38a,#e8e6e0 45%,#b78652)"></div><h4>White Dining Room</h4></article>
    <article class="project"><div class="photo" role="img" aria-label="Living room with large windows" style="background:linear-gradient(120deg,#9ec08a,#e9e4dc 45%,#b8865a)"></div><h4>Living with Large Windows</h4></article>
    <article class="project"><div class="photo" role="img" aria-label="Brown living room with tv wall" style="background:linear-gradient(120deg,#eee,#6a4434 50%,#d8d4cc)"><span class="side-arrow" style="left:0"></span><span class="side-arrow" style="right:0"></span></div><h4 style="margin-top:10px">Brown Living Room</h4></article>
    <article class="project"><div class="photo" role="img" aria-label="Bright living room project" style="background:linear-gradient(120deg,#a2c28c,#e9e4dc 45%,#b8865a)"></div><h4 style="margin-top:10px">Self-Hosted Project</h4></article>
  </section>

  <section class="newsletter">
    <h2 class="section-head" style="top:812px">Newsletter Subscription</h2>
    <div class="rule" style="top:845px;left:0;width:412px"></div>
    <p>Subscribe to our email newsletter for useful tips and valuable resources sent out every second Monday.</p>
    <div class="email">Enter your email address here ...</div>
    <a class="btn" href="#">Subscribe</a>
    <div class="note"><b>*</b> Check your spam folder if the mail does not arrive.</div>
  </section>

  <section class="testimonials">
    <h2 class="section-head" style="top:812px;left:429px">Testimonials <em>– View All Testimonials »</em></h2>
    <div class="pager" style="right:0;top:814px"><b></b><b><svg width="6" height="8"><path d="M1 1 L5 4 L1 7" stroke="#fff" fill="none"/></svg></b></div>
    <div class="rule" style="top:845px;left:429px;width:411px"></div>
    <blockquote class="quote">Lorem ipsum dolor sit amet, consectetuer adipiscing elit, sed diam nonummy nibh euismod tincidunt ut laoreet dolore magna aliquam erat volutpat nibh euismod ut laoreet.</blockquote>
    <div class="author">Nora Whitfield, Lakeshore<span>Brightmill Studio</span></div>
  </section>
</div>

<footer class="footer">
  <div class="copy">Copyright © 2014 Ember-Ridge Builders and Works. All rights reserved.</div>
  <div class="links">Home · Tiles · Systems · Gallery · About us · Contact</div>
  <div class="to-top"><svg width="12" height="8"><path d="M1 7 L6 2 L11 7" stroke="#fff" fill="none" stroke-width="1.5"/></svg></div>
</footer>
</body>
</html>
```